Harvest Gateway Fellowship Ministries needs a fresh new web design

We are an up and coming multicultural church that aims to bring people into a life changing encounter with God. We need a fresh and inviting website in order to increase our internet presence and make us easier to connect with.
Here are some of the basic requirements for the site:
• Clearly displayed address, service times, and contact info
• A staff profile page
• An area for a calendar with upcoming events and their details
• Social media buttons
• Group pages for the different ministries (youth, children’s church, men, etc…)
• An area for donations and eCommerce
• A resources page for assorted media (podcasts, sermons, videos, etc.…)
• An area for prayer requests.

```html
<!DOCTYPE html>
<html lang="en">
<head>
<meta charset="utf-8">
<title>Harvest Gateway Fellowship Ministries – News</title>
<link href="https://fonts.googleapis.com/css2?family=Lato:wght@300;400;700&display=swap" rel="stylesheet">
<style>
:root{
  --navy:#1f1499;
  --gold:#e5c30b;
  --gold-text:#d4a90a;
  --page:#f2f2f2;
  --ink:#555;
  --muted:#7a7a7a;
  --rule:#d6d6d6;
  --foot-text:#c9c6ef;
}
*{margin:0;padding:0;box-sizing:border-box}
html,body{width:1068px;height:1200px;overflow:hidden}
body{font-family:'Lato',sans-serif;background:var(--page);position:relative;color:var(--ink)}
a{color:inherit;text-decoration:none}
.abs{position:absolute}
.nw{white-space:nowrap}

.topbar{top:0;left:0;width:1068px;height:36px;background:var(--navy);color:#fff}
.topbar .motto{left:89px;top:11px;font-size:11.5px}
.topbar .sched-label{right:257px;top:11px;font-size:12px;white-space:nowrap}
.topbar .sched{left:820px;top:5px;border-left:1px solid #fff;padding-left:9px;font-size:10.5px;line-height:13px;white-space:nowrap}

.header{top:36px;left:0;width:1068px;height:102px;background:#fff}
.brand{left:89px;top:20px;width:217px;height:68px;display:flex;align-items:center;gap:8px}
.brand .dot{width:22px;height:22px;border-radius:50%;background:var(--gold);flex:none}
.brand .name{font-size:15px;font-weight:700;color:var(--navy);line-height:18px}
.info{text-align:right;top:20px;white-space:nowrap}
.info h3{font-size:14.5px;font-weight:700;color:#666}
.info p{font-size:12px;color:#666;line-height:13.5px;margin-top:3px}
.info a{display:block;font-size:10.5px;color:var(--gold-text);margin-top:2px}
.vrule{top:24px;width:1px;height:56px;background:#ccc}
.social{left:955px;width:24px;height:24px;border-radius:50%;background:#aaa}

.nav{top:138px;left:0;width:1068px;height:36px;background:var(--gold);font-size:12.5px;color:#333}
.nav .item{top:10px;white-space:nowrap}
.nav .sep{top:11px;width:1px;height:14px;background:rgba(0,0,0,.15)}

.banner{top:174px;left:0;width:1068px;height:89px;background:linear-gradient(90deg,#2a1c08,#5a3e10 40%,#3a2a0c 70%,#2a1d09)}
.banner .crumb{left:89px;top:25px;font-size:11.5px;color:#fff}
.banner .crumb b{font-weight:400}
.banner h1{left:89px;top:39px;font-size:23px;font-weight:700;color:#fff}

.article-title{left:97px;top:314px;width:560px;font-size:20px;font-weight:700;line-height:23px;color:#555}
.article-photo{left:98px;top:374px;width:560px;height:247px;border-radius:3px;background:linear-gradient(135deg,#c9c3b8,#8a7f74 50%,#5d6d8e)}
.article-body{left:98px;top:641px;width:562px;font-size:11.5px;line-height:18px;color:var(--muted);white-space:nowrap}
.article-body p+p{margin-top:17px}
.article-rule{left:98px;top:859px;width:560px;height:1px;background:var(--rule)}
.article-date{left:98px;top:866px;width:560px;text-align:right;font-size:11.5px;color:var(--muted)}

.side-head{left:702px;top:312px;font-size:21px;font-weight:300;color:var(--gold-text)}
.side-rule{left:702px;top:341px;width:268px;height:1px;background:#bbb}
.news-item{left:703px;width:268px;display:flex;gap:17px}
.thumb{width:107px;height:66px;border-radius:2px;background:linear-gradient(135deg,#b8b2aa,#6d7794);flex:none}
.news-item h4{font-size:14.5px;font-weight:700;line-height:16px;color:#666;white-space:nowrap}
.news-item p{font-size:11.5px;line-height:18px;color:var(--muted);margin-top:4px;white-space:nowrap}
.news-text{left:703px;top:467px;width:268px;white-space:nowrap}
.news-text h4{font-size:14.5px;font-weight:700;line-height:18px;color:#555}
.news-text p{font-size:11.5px;line-height:18px;color:var(--muted);margin-top:2px}

.footer{top:931px;left:0;width:1068px;height:269px;background:var(--navy);color:var(--foot-text)}
.footer h5{font-size:17px;font-weight:300;color:#fff;text-transform:uppercase;top:37px;white-space:nowrap}
.footer .col{font-size:11.5px;line-height:16px;white-space:nowrap}
.contact-line{display:flex;align-items:center;gap:9px;font-size:12.5px;margin-top:4px}
.links{list-style:none;font-size:11.5px;line-height:21.3px;white-space:nowrap}
.links li::before{content:"• "}
.email-field{left:533px;top:89px;width:203px;height:30px;background:#fff;border:1px solid #ccc;border-radius:2px;font-size:12px;color:#aaa;padding:7px 11px}
.subscribe{left:533px;top:128px;width:84px;height:31px;background:var(--gold);border-radius:2px;color:#fff;font-size:12.5px;text-align:center;line-height:31px}
.fsocial{top:105px;width:29px;height:29px;border-radius:50%;background:#a7a3d4}
.foot-rule{left:89px;top:201px;width:891px;height:1px;background:#3a30a8}
.copyright{left:0;top:215px;width:1068px;text-align:center;font-size:11px;letter-spacing:.3px}
</style>
</head>
<body>

<div class="topbar abs">
  <div class="motto abs">A house of prayer for all nations, where the love, the presence and the power of God are real.</div>
  <div class="sched-label abs">SUNDAY SERVICE SCHEDULE</div>
  <div class="sched abs">09:00 A.M. | Sunday School<br>10:30 A.M. | Convergent Service</div>
</div>

<header class="header abs">
  <div class="brand abs"><span class="dot"></span><span class="name">Harvest Gateway Fellowship Ministries</span></div>
  <div class="info abs" style="right:559px">
    <h3>Donate</h3><p>Lorem Ipsum is simply<br>dummy text of the printing</p><a href="#">Donate Now »</a>
  </div>
  <div class="vrule abs" style="left:527px"></div>
  <div class="info abs" style="right:308px">
    <h3>Request Prayer</h3><p>Lorem Ipsum is simply dummy text<br>of the printing and typesetting industry.</p><a href="#">Request Now »</a>
  </div>
  <div class="vrule abs" style="left:778px"></div>
  <div class="info abs" style="right:150px">
    <h3>Address</h3><p>Harvest Gateway<br>City, Location</p><a href="#">Contact »</a>
  </div>
  <div class="vrule abs" style="left:936px"></div>
  <span class="social abs" style="top:25px" aria-label="Social link"></span>
  <span class="social abs" style="top:53px" aria-label="Social link"></span>
</header>

<nav class="nav abs">
  <span class="item abs" style="left:103px">Home</span>
  <span class="sep abs" style="left:160px"></span>
  <span class="item abs" style="left:182px">About</span>
  <span class="sep abs" style="left:237px"></span>
  <span class="item abs" style="left:261px">Staff Profile</span>
  <span class="sep abs" style="left:345px"></span>
  <span class="item abs" style="left:372px">News and Events</span>
  <span class="sep abs" style="left:487px"></span>
  <span class="item abs" style="left:510px">Worship &amp; Services</span>
  <span class="sep abs" style="left:637px"></span>
  <span class="item abs" style="left:659px">Groups</span>
  <span class="sep abs" style="left:722px"></span>
  <span class="item abs" style="left:745px">Shop</span>
  <span class="sep abs" style="left:793px"></span>
  <span class="item abs" style="left:818px">Resources</span>
  <span class="sep abs" style="left:896px"></span>
  <span class="item abs" style="left:921px">Contact</span>
</nav>

<section class="banner abs">
  <div class="crumb abs">Home &gt; News and Events &gt; <b>News</b></div>
  <h1 class="abs">News</h1>
</section>

<h2 class="article-title abs">Lorem Ipsum is simply dummy text of the printing and typesetting industry.</h2>
<div class="article-photo abs" role="img" aria-label="Small group reading the Bible together"></div>
<div class="article-body abs">
  <p>Lorem Ipsum is simply dummy text of the printing and typesetting industry. Lorem Ipsum has been the industry's<br>standard dummy text ever since the 1500s, when an unknown printer took a galley of type and scrambled it to<br>make a type specimen book It has survived not only five centuries.</p>
  <p>Also the leap into electronic typesetting, remaining essentially unchanged. It was popularised in the 1960s with<br>the release of Letraset sheets containing Lorem Ipsum passages, and more recently with desktop publishing<br>software like Aldus PageMaker including versions of Lorem Ipsum.</p>
  <p>There are many variations of passages of Lorem Ipsum available, but the majority have suffered alteration in<br>some form, by injected humour, or randomised words which don't look even slightly believable. If you are going<br>to use a passage of Lorem Ipsum, you need to be sure there isn't anything embarrassing hidden.</p>
</div>
<div class="article-rule abs"></div>
<div class="article-date abs">Thursday | July 31, 2014</div>

<h3 class="side-head abs">LATEST NEWS</h3>
<div class="side-rule abs"></div>
<div class="news-item abs" style="top:368px"><div class="thumb" role="img" aria-label="Group study photo"></div><div><h4>Lorem Ipsum is<br>simply dummy..</h4><p>Lorem Ipsum is simply the<br>dummy text of the printing..</p></div></div>
<div class="news-text abs"><h4>Lorem Ipsum is simply dummy text of<br>the printing and typesetting industry.</h4><p>Lorem Ipsum has been the industry's standard<br>dummy text ever since the 1500s, when an unknown<br>printer took a galley of type and scrambled it to make</p></div>
<div class="news-item abs" style="top:589px"><div class="thumb" role="img" aria-label="Group study photo"></div><div><h4>Lorem Ipsum is<br>simply dummy..</h4><p>Lorem Ipsum is simply the<br>dummy text of the printing..</p></div></div>
<div class="news-item abs" style="top:690px"><div class="thumb" role="img" aria-label="Group study photo"></div><div><h4>Lorem Ipsum is<br>simply dummy..</h4><p>Lorem Ipsum is simply the<br>dummy text of the printing..</p></div></div>

<footer class="footer abs">
  <h5 class="abs" style="left:89px">Contact Us</h5>
  <div class="col abs" style="left:89px;top:67px">
    Harvest Gateway<br>Location, city<br>State Name, Country
    <div class="contact-line" style="margin-top:10px"><svg width="13" height="13" viewBox="0 0 24 24"><path fill="#c9c6ef" d="M6.6 10.8a15 15 0 0 0 6.6 6.6l2.2-2.2a1 1 0 0 1 1-.25 11.4 11.4 0 0 0 3.6.57 1 1 0 0 1 1 1V20a1 1 0 0 1-1 1A17 17 0 0 1 3 4a1 1 0 0 1 1-1h3.5a1 1 0 0 1 1 1c0 1.25.2 2.45.57 3.6a1 1 0 0 1-.25 1z"/></svg>+1 555-210-4370</div>
    <div class="contact-line"><svg width="13" height="11" viewBox="0 0 24 18"><rect x="1" y="1" width="22" height="16" fill="none" stroke="#c9c6ef" stroke-width="2"/><path d="M1 1l11 9 11-9" fill="none" stroke="#c9c6ef" stroke-width="2"/></svg>hello@harvestgateway.org</div>
  </div>
  <h5 class="abs" style="left:286px">Communities We Serve</h5>
  <ul class="links abs" style="left:287px;top:64px"><li>Lorem Ipsum</li><li>Dummy Links</li><li>More dummy</li><li>Sample Text</li><li>More samples</li></ul>
  <ul class="links abs" style="left:384px;top:64px"><li>type text dummy</li><li>Lorem Ipsum</li></ul>
  <h5 class="abs" style="left:533px">Newsletter</h5>
  <div class="col abs" style="left:533px;top:67px">Enter your email below to get notified</div>
  <div class="email-field abs">Your Email</div>
  <div class="subscribe abs">Subscribe</div>
  <h5 class="abs" style="left:780px">Connect With Us</h5>
  <div class="col abs" style="left:780px;top:67px">Stay connected for the latest updates at<br>Harvest Gateway Fellowship</div>
  <span class="fsocial abs" style="left:780px" aria-label="Social link"></span>
  <span class="fsocial abs" style="left:816px" aria-label="Social link"></span>
  <div class="foot-rule abs"></div>
  <div class="copyright abs">Copyright © 2014. All rights reserved. Harvest Gateway.</div>
</footer>

</body>
</html>
```